A start up special flyer design!

Hi All - Have updated the attachment content - This is the info required for the designs.
I need a catchy flyer to send out to a few areas to advertise the start of my plumbing business!
The flyer will contain an offer for customers, which will need to have some key details on it. See attached. Feel free to fit these criteria into the flyer given your knowledge on design and messaging principles. Key thing to get across to customers is the discount and special offer, and that it is a start up offer.
I have a logo that needs to be on the flyer as well - let me know what format you require and I will send through to you.
The color scheme needs to be blue / grey / black / white.
Let me know if you have any questions.
I

```html
<!DOCTYPE html>
<html lang="en">
<head>
<meta charset="utf-8">
<title>Local Plumber – Start-up Special Offer</title>
<link rel="stylesheet" href="https://fonts.googleapis.com/css2?family=Archivo+Black&family=Montserrat:ital,wght@0,700;0,800;0,900;1,700&display=swap">
<style>
  :root {
    --sky: #22a6e2;
    --sky-deep: #1a86c4;
    --ring: #1b78b5;
    --navy: #0d2a4a;
    --white: #ffffff;
    --sun: #ffe500;
    --sun-text: #ffe81a;
    --tag-red: #d9202a;
    --tag-red-dark: #9c1219;
    --ink: #111111;
  }
  * { box-sizing: border-box; margin: 0; padding: 0; }
  html, body { width: 850px; height: 1200px; overflow: hidden; }
  body { background: var(--sky); font-family: "Montserrat", Arial, sans-serif; }

  .flyer { position: relative; width: 850px; height: 1200px; overflow: hidden; background: var(--sky); }
  .flyer__edge { position: absolute; top: 0; right: 0; width: 34px; height: 100%; background: var(--sky-deep); }

  .pipe-photo {
    position: absolute; left: 0; top: 640px; width: 850px; height: 560px;
    background:
      radial-gradient(ellipse 260px 280px at 620px 360px, rgba(215,228,238,0.55), transparent 70%),
      linear-gradient(180deg, rgba(34,166,226,0) 0%, #5d89a8 32%, #3c5f7a 68%, #22384c 100%);
  }

  .logo {
    position: absolute; left: 48px; top: 42px; width: 148px; height: 66px;
    background: var(--white); display: flex; align-items: center; justify-content: center;
    font-weight: 900; font-size: 30px; color: var(--ink); letter-spacing: 1px;
  }

  .badge { position: absolute; left: 0; top: 0; }

  .headline {
    position: absolute; left: 275px; top: 255px; width: 300px; text-align: center;
    font-family: "Archivo Black", "Arial Black", sans-serif; color: var(--ink); line-height: 0.98;
  }
  .headline__big { display: block; font-size: 52px; }
  .headline__small { display: block; font-size: 34px; margin: 4px 0 2px; }
  .headline__big .cap { font-size: 62px; }

  .service {
    position: absolute; left: 0; width: 600px; text-align: center; font-weight: 900; color: var(--white);
    -webkit-text-stroke: 1.5px var(--navy); paint-order: stroke fill;
  }
  .service__title { top: 672px; font-size: 27px; letter-spacing: 1px; }
  .service__phone { top: 712px; font-size: 47px; letter-spacing: 1px; }
  .service__scope {
    position: absolute; left: 0; top: 784px; width: 600px; text-align: center;
    font-weight: 800; font-size: 19px; color: var(--navy);
  }

  .offer-band {
    position: absolute; left: 0; top: 828px; width: 612px; height: 94px; background: var(--sun);
    padding: 10px 0 0 50px; color: var(--navy); font-weight: 700; font-style: italic; font-size: 15.5px; line-height: 1.6;
  }

  .appointments { position: absolute; left: 50px; top: 948px; color: var(--white); font-weight: 800; }
  .appointments__title { font-size: 24px; color: var(--navy); text-decoration: underline; text-underline-offset: 3px; margin-bottom: 14px; }
  .appointments__line { font-size: 18.5px; line-height: 1.58; }
  .appointments__value { color: var(--sun-text); }

  .terms { position: absolute; left: 40px; top: 1122px; color: var(--white); font-weight: 700; font-size: 10px; line-height: 1.65; }
</style>
</head>
<body>
<main class="flyer">
  <div class="flyer__edge"></div>
  <div class="pipe-photo" role="img" aria-label="Blurred photograph of a chrome sink drain pipe"></div>

  <div class="logo">LOGO</div>

  <svg class="badge" width="850" height="1000" viewBox="0 0 850 1000">
    <defs>
      <radialGradient id="toolsTone" cx="50%" cy="45%" r="55%">
        <stop offset="0%" stop-color="#ffffff"/>
        <stop offset="62%" stop-color="#f3f5f7"/>
        <stop offset="100%" stop-color="#d7dde2"/>
      </radialGradient>
    </defs>
    <circle cx="428" cy="348" r="306" fill="var(--ring)"/>
    <circle cx="428" cy="348" r="270" fill="url(#toolsTone)" role="img" aria-label="Illustration of a yellow safety helmet above a ring of hand and power tools: saw, hammer, drill, spanners, pliers, grinder"/>
    <circle cx="426" cy="394" r="150" fill="var(--sun)"/>

    <path d="M548 588 C 542 620, 560 650, 585 668" fill="none" stroke="var(--tag-red-dark)" stroke-width="3"/>
    <circle cx="548" cy="588" r="7" fill="var(--sky-deep)" stroke="var(--white)" stroke-width="3"/>

    <g transform="translate(644 780) rotate(62)">
      <path d="M-160 0 L-112 -56 L158 -56 L158 56 L-112 56 Z" fill="var(--tag-red)" stroke="var(--white)" stroke-width="3"/>
      <circle cx="-125" cy="0" r="8" fill="var(--white)"/>
      <text x="22" y="-8" text-anchor="middle" font-family="Montserrat, Arial, sans-serif" font-weight="800" font-size="40" fill="var(--white)" letter-spacing="2">SPECIAL</text>
      <text x="22" y="36" text-anchor="middle" font-family="Montserrat, Arial, sans-serif" font-weight="800" font-size="40" fill="var(--white)" letter-spacing="2">OFFER</text>
    </g>
  </svg>

  <h1 class="headline">
    <span class="headline__big"><span class="cap">Q</span>UALITY</span>
    <span class="headline__big">WORK</span>
    <span class="headline__small">AT A</span>
    <span class="headline__big">DECENT</span>
    <span class="headline__big">PRICE</span>
  </h1>

  <p class="service service__title">LOCAL PLUMBER</p>
  <p class="service service__phone">0400-218-596</p>
  <p class="service__scope">All Plumbing, Draining and Gasfitting Works</p>

  <div class="offer-band">
    <p>15% off your overall bill*</p>
    <p>No GST payable, saving you additional 10% on your bill**</p>
    <p>Plus, a free hot water health check and replacement quote***</p>
  </div>

  <section class="appointments">
    <h2 class="appointments__title">FOR APPOINTMENTS:</h2>
    <p class="appointments__line">Call us at: <span class="appointments__value">0400-218-596</span></p>
    <p class="appointments__line">Email us at: <span class="appointments__value">hello@brightflowplumbing.com</span></p>
    <p class="appointments__line">Book directly on our website at: <span class="appointments__value">www.brightflowplumbing.com</span></p>
  </section>

  <div class="terms">
    <p>*Offer valid between 15 August 2016 to 15 October 2016</p>
    <p>**Valid until 30 September 2016.</p>
    <p>***Quote valid for 12 months from the quote date.</p>
  </div>
</main>
</body>
</html>
```